KLVB Canberra Pty Ltd

Want something creative and that catches your eye. We are a traffic control companythat offers all aspects of traffic control from planning to roadworks.

Contact Information for Business Card

Derek Oswin - Director
Ph: 0418 372 506
Email: derek@klvb-example.com.au
27 Wattle Grove ct Banfield ACT 2911

```html
<!DOCTYPE html>
<html lang="en">
<head>
<meta charset="utf-8">
<title>KLVB Canberra – Business Card</title>
<link rel="stylesheet" href="https://fonts.googleapis.com/css2?family=Michroma&display=swap">
<style>
  :root {
    --backdrop: #3a3a3c;
    --card: #262626;
    --silver: #e6e6e6;
    --gold: #b6a42c;
    --gold-light: #d4c244;
    --gold-dark: #8c7a16;
    --muted: #cfcfcf;
  }
  * { box-sizing: border-box; margin: 0; padding: 0; }
  html, body { width: 1200px; height: 900px; overflow: hidden; }
  body {
    background: var(--backdrop);
    font-family: "Michroma", "Arial", sans-serif;
    display: flex;
    flex-direction: column;
    align-items: center;
    justify-content: center;
    gap: 60px;
  }
  .card {
    position: relative;
    width: 560px;
    height: 340px;
    background: var(--card);
    overflow: hidden;
  }
  .hazard-panel {
    position: absolute;
    top: 0;
    right: 0;
    width: 170px;
    height: 100%;
    background: linear-gradient(100deg, var(--card) 0%, var(--gold-dark) 45%, var(--gold-light) 100%);
    opacity: 0.85;
  }
  .card-front .brand {
    position: absolute;
    left: 40px;
    top: 120px;
    display: flex;
    align-items: center;
    gap: 14px;
  }
  .brand-mark {
    width: 58px;
    height: 58px;
    border-radius: 50%;
    background: var(--gold);
  }
  .brand-text { display: flex; flex-direction: column; }
  .brand-name {
    font-size: 30px;
    color: var(--silver);
    letter-spacing: 1px;
    line-height: 1;
  }
  .brand-person {
    margin-top: 8px;
    font-size: 11px;
    color: var(--silver);
    letter-spacing: 1px;
  }
  .brand-role {
    margin-top: 4px;
    font-size: 9px;
    color: var(--gold);
    letter-spacing: 2px;
    padding-left: 18px;
  }
  .card-back .holder {
    position: absolute;
    left: 44px;
    top: 100px;
  }
  .holder-name {
    font-size: 26px;
    font-weight: 400;
    color: var(--silver);
    letter-spacing: 2px;
  }
  .holder-role {
    margin-top: 4px;
    padding-left: 40px;
    font-size: 20px;
    color: var(--gold);
    letter-spacing: 2px;
  }
  .contact {
    position: absolute;
    left: 44px;
    bottom: 34px;
    list-style: none;
    font-size: 10.5px;
    line-height: 1.45;
    color: var(--muted);
    text-transform: uppercase;
    letter-spacing: 0.5px;
  }
</style>
</head>
<body>

<section class="card card-front">
  <div class="hazard-panel" role="img" aria-label="Gold hazard stripe decoration along the right edge"></div>
  <div class="brand">
    <span class="brand-mark"></span>
    <div class="brand-text">
      <span class="brand-name">KLVB</span>
      <span class="brand-person">DEREK OSWIN</span>
      <span class="brand-role">DIRECTOR</span>
    </div>
  </div>
</section>

<section class="card card-back">
  <div class="hazard-panel" role="img" aria-label="Gold hazard stripe decoration along the right edge"></div>
  <div class="holder">
    <h1 class="holder-name">DEREK OSWIN</h1>
    <p class="holder-role">DIRECTOR</p>
  </div>
  <ul class="contact">
    <li>Ph: 0418 372 506</li>
    <li>Email: derek@klvb-example.com.au</li>
    <li>27 Wattle Grove ct Banfield ACT 2911</li>
  </ul>
</section>

</body>
</html>
```